MRT Property - Business Cards

Looking for a business card & general letterhead, signage etc design for our new logo.

Colours:
000a20
0056a2
00b5ef
0088ce
68cef2

Fonts:
Poppins
Karla

Please keep look and feel of new brand - example in the zip package I sent.

```html
<!DOCTYPE html>
<html lang="en">
<head>
<meta charset="utf-8">
<title>MRT Property – Business Cards</title>
<link rel="stylesheet" href="https://fonts.googleapis.com/css2?family=Poppins:wght@400;500;600&family=Open+Sans:wght@400;700&display=swap">
<style>
  :root {
    --ink: #000a20;
    --brand-deep: #0056a2;
    --brand-bright: #00b5ef;
    --brand-mid: #0088ce;
    --brand-light: #68cef2;
    --card: #eceef2;
    --stage: #d5d5d5;
  }
  * { box-sizing: border-box; margin: 0; padding: 0; }
  html, body { width: 1200px; height: 780px; overflow: hidden; }
  body {
    background: var(--stage);
    display: flex;
    align-items: center;
    justify-content: center;
    gap: 40px;
    font-family: "Poppins", sans-serif;
    color: var(--ink);
  }
  .card {
    position: relative;
    width: 540px;
    height: 330px;
    background: var(--card);
    box-shadow: 0 10px 30px rgba(0,0,0,.18);
  }

  /* Back: contact side */
  .card--contact .wordmark {
    position: absolute;
    left: 42px;
    top: 104px;
    display: flex;
    align-items: center;
    gap: 10px;
  }
  .wordmark__dot {
    width: 18px; height: 18px;
    border-radius: 50%;
    background: var(--brand-bright);
  }
  .wordmark__name {
    font-family: "Poppins", sans-serif;
    font-weight: 600;
    color: var(--brand-deep);
    font-size: 28px;
    letter-spacing: .5px;
    white-space: nowrap;
  }
  .divider {
    position: absolute;
    left: 262px;
    top: 72px;
    width: 1.5px;
    height: 150px;
    background: var(--brand-mid);
  }
  .person {
    position: absolute;
    left: 286px;
    top: 80px;
  }
  .person__name {
    font-family: "Open Sans", sans-serif;
    font-size: 30px;
    line-height: 1.1;
    color: var(--brand-deep);
    white-space: nowrap;
  }
  .person__first { font-weight: 700; }
  .person__last { font-weight: 400; }
  .person__title {
    font-weight: 600;
    font-size: 13px;
    margin-top: 2px;
  }
  .contact-list {
    list-style: none;
    margin-top: 16px;
    font-size: 13.5px;
    line-height: 1.65;
  }
  .contact-list li { display: flex; align-items: center; gap: 8px; white-space: nowrap; }
  .contact-list svg { width: 13px; height: 13px; flex: none; }
  .address {
    position: absolute;
    left: 42px;
    bottom: 34px;
    font-size: 13px;
    white-space: nowrap;
  }

  /* Front: brand side */
  .card--front {
    display: flex;
    align-items: center;
    justify-content: center;
  }
  .card--front .wordmark { display: flex; align-items: center; gap: 18px; }
  .card--front .wordmark__dot { width: 34px; height: 34px; }
  .card--front .wordmark__name { font-size: 54px; }
</style>
</head>
<body>

  <section class="card card--contact">
    <div class="wordmark">
      <span class="wordmark__dot"></span>
      <span class="wordmark__name">MRT Property</span>
    </div>
    <span class="divider"></span>
    <div class="person">
      <p class="person__name"><span class="person__first">Callum</span> <span class="person__last">Reid</span></p>
      <p class="person__title">Director</p>
      <ul class="contact-list">
        <li>
          <svg viewBox="0 0 16 16" aria-hidden="true"><path fill="var(--brand-light)" d="M3.5 1.5l2.2 0 1 3.2-1.6 1.2a8 8 0 0 0 4.9 4.9l1.2-1.6 3.2 1v2.2a1.6 1.6 0 0 1-1.7 1.6A12.5 12.5 0 0 1 1.9 3.2 1.6 1.6 0 0 1 3.5 1.5z"/></svg>
          +61 2 9000 4821
        </li>
        <li>
          <svg viewBox="0 0 16 16" aria-hidden="true"><circle cx="8" cy="8" r="7" fill="var(--brand-light)"/><path d="M1 8h14M8 1c-3 3.5-3 10.5 0 14M8 1c3 3.5 3 10.5 0 14" stroke="#fff" stroke-width="1" fill="none"/></svg>
          www.mrtproperty.com.au
        </li>
        <li>
          <svg viewBox="0 0 16 16" aria-hidden="true"><rect x="1" y="3" width="14" height="10" rx="1.5" fill="var(--brand-light)"/><path d="M1.5 4l6.5 5 6.5-5" stroke="#fff" stroke-width="1.2" fill="none"/></svg>
          hello@mrtproperty.com.au
        </li>
      </ul>
    </div>
    <p class="address">Suite 4.12, Level 3 18 Harbour Lane Riverside NSW 2150</p>
  </section>

  <section class="card card--front">
    <div class="wordmark">
      <span class="wordmark__dot"></span>
      <span class="wordmark__name">MRT Property</span>
    </div>
  </section>

</body>
</html>
```